German Headhunter/ HR Consultancy needs Business Cards Design

We need a business Card Design for our Company in Stuttgart. We are specialized as Headhunter/ HR Consultancy in Placement of specialist and managers in permanent employment. Please refer to our business logo.

```html
<!DOCTYPE html>
<html lang="en">
<head>
<meta charset="utf-8">
<title>Kernwerk Personalberatung – Business Cards</title>
<link rel="stylesheet" href="https://fonts.googleapis.com/css2?family=Montserrat:wght@400;500;600;700&display=swap">
<style>
  :root {
    --brand-blue: #2a43a0;
    --brand-blue-deep: #22398f;
    --ink-grey: #6e6e6e;
    --paper: #ffffff;
    --backdrop: #d9dadc;
    --on-blue: #ffffff;
    --on-blue-muted: #b9c2e6;
  }
  * { box-sizing: border-box; margin: 0; padding: 0; }
  html, body { width: 1200px; height: 800px; overflow: hidden; }
  body {
    background: var(--backdrop);
    font-family: "Montserrat", sans-serif;
    display: flex;
    align-items: center;
    justify-content: center;
    gap: 60px;
  }
  .card {
    position: relative;
    width: 525px;
    height: 300px;
    border-radius: 16px;
    overflow: hidden;
    box-shadow: 0 10px 24px rgba(0,0,0,.18);
  }

  /* Front */
  .card--front { background: var(--paper); }
  .card__corner {
    position: absolute;
    top: 0; right: 0;
    width: 100%; height: 100%;
  }
  .front__content {
    position: absolute;
    left: 38px; top: 40px;
  }
  .wordmark__name {
    font-weight: 700;
    font-size: 34px;
    letter-spacing: 1px;
    color: var(--brand-blue);
    line-height: 1;
  }
  .wordmark__sub {
    font-weight: 700;
    font-size: 14px;
    letter-spacing: 2.2px;
    color: var(--ink-grey);
    margin-top: 4px;
  }
  .person { margin-top: 22px; }
  .person__name {
    font-weight: 700;
    font-size: 17px;
    letter-spacing: 1px;
    color: var(--brand-blue);
  }
  .person__role {
    font-size: 11px;
    color: var(--ink-grey);
    margin-top: 2px;
  }
  .contact { list-style: none; margin-top: 14px; }
  .contact__item {
    display: flex;
    align-items: flex-start;
    gap: 9px;
    font-size: 10.5px;
    color: var(--ink-grey);
    line-height: 1.45;
  }
  .contact__icon {
    width: 11px; height: 11px;
    margin-top: 2px;
    flex: none;
    fill: var(--brand-blue);
  }
  .card__edge-mark {
    position: absolute;
    left: 0; bottom: 44px;
    width: 8px; height: 18px;
    background: var(--ink-grey);
    opacity: .5;
  }

  /* Back */
  .card--back {
    background: linear-gradient(135deg, var(--brand-blue) 0%, var(--brand-blue-deep) 100%);
    color: var(--on-blue);
  }
  .back__brand {
    position: absolute;
    left: 0; right: 0; top: 92px;
    display: flex;
    align-items: center;
    justify-content: center;
    gap: 14px;
  }
  .back__square {
    width: 44px; height: 44px;
    background: var(--on-blue-muted);
  }
  .back__divider {
    width: 2px; height: 62px;
    background: var(--on-blue-muted);
    opacity: .6;
  }
  .back__wordmark-name {
    font-weight: 700;
    font-size: 34px;
    letter-spacing: 1px;
    color: var(--on-blue);
    line-height: 1;
  }
  .back__wordmark-sub {
    font-weight: 700;
    font-size: 14px;
    letter-spacing: 2.2px;
    color: var(--on-blue);
    margin-top: 4px;
  }
  .back__tagline {
    position: absolute;
    left: 40px; right: 40px; bottom: 42px;
    text-align: center;
    font-size: 11.5px;
    line-height: 1.5;
    color: var(--on-blue);
  }
</style>
</head>
<body>

  <section class="card card--front" aria-label="Business card front">
    <svg class="card__corner" viewBox="0 0 525 300" preserveAspectRatio="none" aria-hidden="true">
      <polygon points="300,0 525,0 525,205" fill="var(--brand-blue)"/>
    </svg>

    <div class="front__content">
      <div class="wordmark">
        <div class="wordmark__name">KERNWERK</div>
        <div class="wordmark__sub">PERSONALBERATUNG</div>
      </div>

      <div class="person">
        <div class="person__name">JONAS BRANDT</div>
        <div class="person__role">Founder &amp; CEO</div>
      </div>

      <ul class="contact">
        <li class="contact__item">
          <svg class="contact__icon" viewBox="0 0 12 12"><path d="M6 0a4 4 0 0 0-4 4c0 3 4 8 4 8s4-5 4-8a4 4 0 0 0-4-4zm0 5.5A1.5 1.5 0 1 1 6 2.5a1.5 1.5 0 0 1 0 3z"/></svg>
          <span>24 Lindenweg<br>Stuttgart 70173</span>
        </li>
        <li class="contact__item">
          <svg class="contact__icon" viewBox="0 0 12 12"><path d="M2.5 0.5l2 2.5-1.2 1.5a7 7 0 0 0 4.2 4.2L9 7.5l2.5 2-1.5 2C5 11.5.5 7 .5 2z"/></svg>
          <span>0711-482-3370</span>
        </li>
        <li class="contact__item">
          <svg class="contact__icon" viewBox="0 0 12 12"><rect x="1" y="1" width="10" height="10" rx="1" fill="none" stroke="var(--brand-blue)" stroke-width="1.5"/></svg>
          <span>0711-482-3371</span>
        </li>
        <li class="contact__item">
          <svg class="contact__icon" viewBox="0 0 12 12"><rect x="3" y="0" width="6" height="12" rx="1"/><rect x="4.5" y="9.5" width="3" height="1" fill="#fff"/></svg>
          <span>0170-559-2846</span>
        </li>
        <li class="contact__item">
          <svg class="contact__icon" viewBox="0 0 12 12"><rect x="0" y="2" width="12" height="8" rx="1"/><path d="M0.5 2.5L6 7l5.5-4.5" fill="none" stroke="#fff" stroke-width="1"/></svg>
          <span>jonas@kernwerk-hr.com</span>
        </li>
        <li class="contact__item">
          <svg class="contact__icon" viewBox="0 0 12 12"><circle cx="6" cy="6" r="6"/><path d="M0 6h12M6 0c-3 3-3 9 0 12M6 0c3 3 3 9 0 12" fill="none" stroke="#fff" stroke-width=".8"/></svg>
          <span>www.kernwerk-hr.com</span>
        </li>
      </ul>
    </div>
    <div class="card__edge-mark" aria-hidden="true"></div>
  </section>

  <section class="card card--back" aria-label="Business card back">
    <div class="back__brand">
      <div class="back__square" aria-hidden="true"></div>
      <div class="back__divider" aria-hidden="true"></div>
      <div class="back__wordmark">
        <div class="back__wordmark-name">KERNWERK</div>
        <div class="back__wordmark-sub">PERSONALBERATUNG</div>
      </div>
    </div>
    <p class="back__tagline">We are specialized as Headhunter/ HR Consultancy in Placement of<br>specialist and managers in permanent employment.</p>
  </section>

</body>
</html>
```